Merry Meadow Roasters

We need a website to sell coffee with a horse theme. We already have a logo and have designed 4 different coffee bags/flavors so far, each of which will be available in ground or whole bean. The brand is intended to be light hearted/whimsical.

Requirements
Must have
• incorporation of attached photos
Nice to have
• underlying background theme with sky/grass

```html
<!DOCTYPE html>
<html lang="en">
<head>
<meta charset="utf-8">
<title>Merry Meadow Roasters</title>
<link href="https://fonts.googleapis.com/css2?family=Poppins:ital,wght@0,400;0,500;0,600;0,700;1,400&family=Lato:ital,wght@0,400;0,700;1,400&display=swap" rel="stylesheet">
<style>
:root{
  --cream:#fdf6ee;
  --cream-band:#fdeedd;
  --caramel:#e0a46c;
  --caramel-deep:#d8965a;
  --espresso:#3a2414;
  --roast:#4a2d18;
  --ink:#2b1d12;
  --body:#3d3d3d;
  --muted:#6a6a6a;
  --star:#f5b301;
  --line:#d9d0c6;
}
*{margin:0;padding:0;box-sizing:border-box}
html,body{width:1200px;height:3393px;overflow:hidden;background:#fff}
body{position:relative;font-family:'Lato',sans-serif;color:var(--body)}
.abs{position:absolute}
h1,h2,h3,h4,.nav a,.btn,.brand{font-family:'Poppins',sans-serif}
.accent{color:var(--caramel)}
.btn{position:absolute;display:flex;align-items:center;justify-content:center;border-radius:30px;font-weight:600;font-size:15px;text-decoration:none}
.btn-dark{background:var(--espresso);color:var(--caramel)}
.btn-news{background:var(--espresso);color:#fff;font-size:14px}
.btn-light{background:var(--caramel);color:var(--espresso)}
.ph{position:absolute}

/* header */
.hero-band{left:0;top:0;width:1200px;height:345px;background:var(--cream)}
.brand{font-weight:600;color:var(--espresso);font-size:22px;line-height:1.15;text-align:center}
.topmail{right:380px;top:24px;font-size:15px;color:var(--ink);display:flex;align-items:center;gap:8px;font-family:'Poppins',sans-serif;white-space:nowrap}
.callbox{left:847px;top:0;width:241px;height:57px;background:var(--caramel);display:flex;align-items:center;padding-left:28px;gap:12px}
.callbox small{display:block;font-size:11px;color:var(--espresso);font-family:'Poppins',sans-serif}
.callbox b{display:block;font-size:17px;color:var(--espresso);font-family:'Poppins',sans-serif;font-weight:600}
.nav{top:85px;left:0;width:1200px;height:24px}
.nav a{position:absolute;font-size:15px;color:var(--ink);text-decoration:none;font-weight:500}
.nav a.active{color:var(--caramel)}
.hero-title{left:110px;top:196px;font-size:48px;line-height:61px;font-weight:600;color:var(--caramel)}
.hero-copy{left:110px;top:368px;width:470px;font-size:14.5px;line-height:31px;color:var(--ink)}

/* products */
.sec-title{width:1200px;left:0;text-align:center;font-weight:600;color:var(--ink)}
.sec-copy{width:1200px;left:0;text-align:center;font-size:15px;line-height:31px;color:var(--ink)}
.product{position:absolute;width:260px;text-align:center}
.product .shot{width:237px;height:237px;margin:0 auto;border-radius:6px;background:linear-gradient(180deg,#f7dba4 0%,#e7b86c 60%,#5a3720 100%)}
.product h4{margin-top:33px;font-size:17px;font-weight:500;color:var(--ink)}
.stars{color:var(--star);font-size:15px;letter-spacing:1px;margin-top:6px}

/* about */
.about-dark{left:600px;top:1288px;width:600px;height:481px;background:var(--roast)}
.about-title{left:662px;top:1355px;font-size:44px;line-height:61px;font-weight:600;color:#fff;white-space:nowrap}
.about-copy{left:662px;top:1489px;width:430px;font-size:15px;line-height:31px;color:#fff}

/* testimonials */
.quote-mark{left:110px;top:1820px;font-family:'Poppins',sans-serif;font-weight:700;font-size:330px;line-height:1;color:#f3ece5}
.say-title{left:137px;top:1935px;font-size:46px;line-height:57px;font-weight:600;color:var(--ink)}
.say-copy{left:155px;top:2116px;width:260px;font-size:14px;line-height:26px;color:var(--muted)}
.card{left:544px;top:1937px;width:544px;height:273px;background:#fff;border-radius:10px;box-shadow:0 6px 30px rgba(0,0,0,.09)}
.avatar{left:53px;top:29px;width:66px;height:66px;border-radius:50%;background:linear-gradient(160deg,#c98c63,#7a4a2e)}
.card h3{position:absolute;left:136px;top:34px;font-size:21px;font-weight:600;color:var(--ink)}
.card .loc{position:absolute;left:139px;top:64px;font-size:13px;color:var(--ink);font-family:'Poppins',sans-serif}
.card .rate{position:absolute;left:136px;top:83px;display:flex;align-items:center;gap:6px}
.card .date{font-size:13px;color:var(--ink);margin-left:10px;font-family:'Poppins',sans-serif}
.card p{position:absolute;left:46px;top:140px;width:460px;font-size:12.5px;line-height:21px;font-style:italic;color:#5a5a5a}
.arrow{position:absolute;top:2254px;width:44px;height:44px;border-radius:50%;background:#fff;box-shadow:0 3px 14px rgba(0,0,0,.12);display:flex;align-items:center;justify-content:center}

/* news */
.news-band{left:0;top:2397px;width:1200px;height:580px;background:linear-gradient(180deg,var(--cream-band) 0%,#fff 100%)}
.news{position:absolute;top:2539px;width:318px}
.news .pic{position:relative;height:200px}
.news .date-tag{position:absolute;left:12px;top:12px;width:52px;height:52px;background:var(--caramel);text-align:center;font-family:'Poppins',sans-serif;color:var(--ink)}
.news .date-tag b{display:block;font-size:17px;font-weight:600;line-height:26px;padding-top:3px}
.news .date-tag span{display:block;font-size:10px}
.news h4{margin-top:16px;font-size:17.5px;font-weight:600;color:var(--ink)}
.news p{margin-top:6px;font-size:14.5px;line-height:23px;color:#555}

/* footer */
.rule{left:110px;width:978px;height:1px;background:var(--line)}
.foot-h{font-size:20px;font-weight:600;color:var(--ink);font-family:'Poppins',sans-serif}
.foot-list{list-style:none}
.foot-list li{font-size:15px;color:var(--ink);height:34px;line-height:20px}
.social{position:absolute;top:3218px;width:28px;height:28px;border-radius:50%;border:1.5px solid var(--ink);display:flex;align-items:center;justify-content:center}
.contact-row{position:absolute;left:847px;display:flex;gap:12px;font-size:15px;line-height:27px;color:var(--ink)}
.ic{width:32px;height:32px;border-radius:50%;background:var(--espresso);display:flex;align-items:center;justify-content:center;flex-shrink:0}
.copyright{left:0;width:1200px;top:3335px;text-align:center;font-size:15px;color:var(--ink)}
</style>
</head>
<body>

<!-- Header & hero -->
<div class="abs hero-band"></div>
<div class="abs brand" style="left:100px;top:78px;width:190px">Merry Meadow<br>Roasters</div>

<div class="abs topmail">
  <svg width="14" height="11" viewBox="0 0 14 11"><rect x="0.5" y="0.5" width="13" height="10" rx="1" fill="var(--ink)"/><path d="M1 1.5l6 4.5 6-4.5" stroke="#fff" stroke-width="1.2" fill="none"/></svg>
  hello@merrymeadowroasters.com
</div>
<div class="abs callbox">
  <div class="ic" style="width:30px;height:30px;background:var(--espresso)">
    <svg width="15" height="15" viewBox="0 0 24 24"><path fill="#fff" d="M6.6 10.8a15 15 0 006.6 6.6l2.2-2.2c.3-.3.7-.4 1-.2 1.1.4 2.3.6 3.6.6.6 0 1 .4 1 1V20c0 .6-.4 1-1 1A17 17 0 013 4c0-.6.4-1 1-1h3.5c.6 0 1 .4 1 1 0 1.3.2 2.5.6 3.6.1.3 0 .7-.2 1L6.6 10.8z"/></svg>
  </div>
  <div><small>Call Us :</small><b>+1 555 010 2040</b></div>
</div>

<nav class="abs nav">
  <a class="active" style="left:349px">Home</a>
  <a style="left:457px">Tea Products</a>
  <a style="left:623px">Sell Coffee</a>
  <a style="left:757px">Testimonials</a>
  <a style="left:919px">Blog</a>
  <a style="left:1018px">About Us</a>
</nav>

<h1 class="abs hero-title">Wake Up &amp; Smell the<br>Coffee</h1>
<p class="abs hero-copy">Lorem ipsum dolor sit amet, consectetur adipiscing elit, sed ipsum dolor sit amet, consecteturdo eiusmod tempor incididunt ut labore ipsum dolor sit amet, consecteturet dolore magna aliqua.</p>
<a class="btn btn-dark" style="left:110px;top:478px;width:163px;height:57px">Get Started</a>

<div class="ph" role="img" aria-label="Coffee bag with horse and cowboy artwork surrounded by roasted coffee beans" style="left:690px;top:158px;width:425px;height:428px;border-radius:14px;background:linear-gradient(180deg,#f6d9a0 0%,#e8b46a 55%,#6a4226 100%)"></div>
<div class="ph" role="img" aria-label="Illustration of a cowboy riding a horse over a barrel" style="left:1034px;top:204px;width:166px;height:217px;border-radius:10px;background:linear-gradient(160deg,#f3e1c8,#c79a6a)"></div>

<!-- Products -->
<div class="ph" role="img" aria-label="Illustration of a rider on a bucking horse" style="left:13px;top:599px;width:178px;height:207px;border-radius:10px;background:linear-gradient(160deg,#f2e4d2,#a9795a)"></div>
<h2 class="abs sec-title" style="top:694px;font-size:45px">Our Tea <span class="accent">Products</span></h2>
<p class="abs sec-copy" style="top:759px">Duis aute irure dolor in reprehenderit in voluptate velit esse cillum dolore eu fugiat nulla pariatur. Excepteur sint<br>occaecat cupidatat non proident, sunt in culpa qui officia deserunt mollit anim id est laborum.</p>

<div class="product" style="left:70px;top:856px"><div class="shot" role="img" aria-label="Trail Trotter coffee bag with beans"></div><h4>Trail Trotter</h4><div class="stars">★★★★★</div></div>
<div class="product" style="left:338px;top:856px"><div class="shot" role="img" aria-label="Gentle Canter coffee bag with beans"></div><h4>Gentle Canter</h4><div class="stars">★★★★★</div></div>
<div class="product" style="left:594px;top:856px"><div class="shot" role="img" aria-label="High Fence Blend coffee bag with beans"></div><h4>High Fence Blend</h4><div class="stars">★★★★★</div></div>
<div class="product" style="left:860px;top:856px"><div class="shot" role="img" aria-label="Barrel Dash coffee bag with beans"></div><h4>Barrel Dash</h4><div class="stars">★★★★★</div></div>

<!-- About -->
<div class="ph" role="img" aria-label="Photo of a smiling woman holding a coffee cup" style="left:0;top:1258px;width:600px;height:511px;background:linear-gradient(135deg,#c9b49a 0%,#a4643e 50%,#5a3a24 100%)"></div>
<div class="abs about-dark"></div>
<h2 class="abs about-title">About Merry <span class="accent">Meadow</span><br><span class="accent">Roasters</span></h2>
<p class="abs about-copy">Lorem ipsum dolor sit amet, consectetur adipiscing elit, sed do eiusmod tempor incididunt ut labore et dolore magna aliqua. Ut enim ad minim veniam, quis nostrud exercitation ullamco labois nisi ut aliquip ex ea commodo consequat.</p>
<a class="btn btn-light" style="left:664px;top:1642px;width:156px;height:53px">Read More</a>

<!-- Testimonials -->
<div class="abs quote-mark">“</div>
<h2 class="abs say-title">What<br>Our <span class="accent">Customer</span><br><span class="accent">Says</span></h2>
<p class="abs say-copy">Quis autem vel eum iure reprehend erit qui in ea voluptate velit esse quam nihil molestiae.......</p>
<div class="ph" role="img" aria-label="Illustration of a rider jumping a horse over a fence" style="left:500px;top:1818px;width:172px;height:190px;border-radius:10px;background:linear-gradient(160deg,#f1e4d3,#b58a63)"></div>
<div class="abs card">
  <div class="abs avatar" role="img" aria-label="Customer portrait"></div>
  <h3>Nora Whitfield</h3>
  <div class="loc">Villmar, Germany</div>
  <div class="rate"><span class="stars" style="font-size:24px;margin:0;letter-spacing:3px">★★★★★</span><span class="date">Jan 16, 2025</span></div>
  <p>Sed ut perspiciatis unde omnis iste natus error sit voluptatem accusantium doloremque laudantium, totam rem aperiam, eaque ipsa quae ab illo inventore veritatis et quasi architecto beatae vitae dicta sunt explicabo. Totam rem aperiam, eaque ipsa quae ab illo inventore .</p>
</div>
<div class="arrow" style="left:976px"><svg width="10" height="14" viewBox="0 0 10 14"><path d="M7 2L2 7l5 5" stroke="var(--ink)" stroke-width="1.8" fill="none"/></svg></div>
<div class="arrow" style="left:1045px"><svg width="10" height="14" viewBox="0 0 10 14"><path d="M3 2l5 5-5 5" stroke="var(--ink)" stroke-width="1.8" fill="none"/></svg></div>

<!-- News -->
<div class="abs news-band"></div>
<h2 class="abs sec-title" style="top:2455px;font-size:45px">Latest <span class="accent">News</span></h2>

<article class="news" style="left:110px">
  <div class="pic" role="img" aria-label="Photo of friends chatting over coffee" style="background:linear-gradient(135deg,#e6e2dc,#6c7a6a)"><div class="date-tag"><b>12</b><span>Dec 24</span></div></div>
  <h4>Lorem ipsum dolor sit amet</h4>
  <p>Excepteur sint occaecat cupidatat non proid ent, sunt in culpa qui...</p>
</article>
<article class="news" style="left:441px">
  <div class="pic" role="img" aria-label="Photo of a woman sipping from a white cup in a cafe" style="background:linear-gradient(135deg,#3a2a20,#b07050 60%,#e8d6c6)"><div class="date-tag"><b>10</b><span>Jan 25</span></div></div>
  <h4>Orem ipsum dolor sit amet</h4>
  <p>Excepteur sint occaecat cupidatat non proid ent, sunt in culpa qui...</p>
</article>
<article class="news" style="left:770px">
  <div class="pic" role="img" aria-label="Photo of hands holding cups of coffee" style="background:linear-gradient(135deg,#d8d0c8,#8a6a52 60%,#4a3628)"><div class="date-tag"><b>19</b><span>Jan 24</span></div></div>
  <h4>Rem ipsum dolor sit amet</h4>
  <p>Excepteur sint occaecat cupidatat non proid ent, sunt in culpa qui...</p>
</article>
<a class="btn btn-news" style="left:110px;top:2843px;width:125px;height:41px">Read More</a>
<a class="btn btn-news" style="left:441px;top:2843px;width:125px;height:41px">Read More</a>
<a class="btn btn-news" style="left:770px;top:2843px;width:125px;height:41px">Read More</a>

<!-- Footer -->
<div class="ph" role="img" aria-label="Illustration of a rider on a grey horse" style="left:0;top:2904px;width:142px;height:197px;border-radius:10px;background:linear-gradient(160deg,#ece6df,#8e8a88)"></div>
<div class="abs rule" style="top:2990px"></div>

<div class="abs brand" style="left:135px;top:3110px;width:190px">Merry Meadow<br>Roasters</div>
<div class="social" style="left:131px"><svg width="10" height="12" viewBox="0 0 10 12"><circle cx="5" cy="6" r="3" fill="var(--ink)"/></svg></div>
<div class="social" style="left:180px"><svg width="10" height="12" viewBox="0 0 10 12"><circle cx="5" cy="6" r="3" fill="var(--ink)"/></svg></div>
<div class="social" style="left:228px"><svg width="10" height="12" viewBox="0 0 10 12"><circle cx="5" cy="6" r="3" fill="var(--ink)"/></svg></div>
<div class="social" style="left:277px"><svg width="10" height="12" viewBox="0 0 10 12"><circle cx="5" cy="6" r="3" fill="var(--ink)"/></svg></div>

<div class="abs" style="left:423px;top:3049px">
  <h4 class="foot-h" style="margin-bottom:20px">Quick Links</h4>
  <ul class="foot-list" style="padding-left:3px"><li>Home</li><li>About</li><li>Sell Tea</li><li>Testimonials</li><li>Contact us</li></ul>
</div>
<div class="abs" style="left:643px;top:3049px">
  <h4 class="foot-h" style="margin-bottom:20px">Help Links</h4>
  <ul class="foot-list"><li>FAQ</li><li>Terms of use</li><li>Privacy Policy</li><li>Support Links</li><li>Conditions</li></ul>
</div>
<div class="abs" style="left:847px;top:3049px"><h4 class="foot-h">Contact Us</h4></div>
<div class="contact-row" style="top:3093px">
  <div class="ic"><svg width="12" height="16" viewBox="0 0 12 16"><path d="M6 0a6 6 0 016 6c0 4.5-6 10-6 10S0 10.5 0 6a6 6 0 016-6z" fill="#fff"/><circle cx="6" cy="6" r="2.2" fill="var(--espresso)"/></svg></div>
  <div>Merry Meadow Roasters<br>United States</div>
</div>
<div class="contact-row" style="top:3164px;align-items:center">
  <div class="ic"><svg width="14" height="14" viewBox="0 0 24 24"><path fill="#fff" d="M6.6 10.8a15 15 0 006.6 6.6l2.2-2.2c.3-.3.7-.4 1-.2 1.1.4 2.3.6 3.6.6.6 0 1 .4 1 1V20c0 .6-.4 1-1 1A17 17 0 013 4c0-.6.4-1 1-1h3.5c.6 0 1 .4 1 1 0 1.3.2 2.5.6 3.6.1.3 0 .7-.2 1L6.6 10.8z"/></svg></div>
  <div>+1 555 010 2040</div>
</div>
<div class="contact-row" style="top:3215px;align-items:center">
  <div class="ic"><svg width="14" height="11" viewBox="0 0 14 11"><rect x="0.5" y="0.5" width="13" height="10" rx="1" fill="#fff"/><path d="M1 1.5l6 4.5 6-4.5" stroke="var(--espresso)" stroke-width="1.2" fill="none"/></svg></div>
  <div>hello@merrymeadowroasters.com</div>
</div>

<div class="abs rule" style="top:3299px"></div>
<p class="abs copyright">Copyrights@2024.Merry Meadow Roasters.All Rights Reserved</p>

</body>
</html>
```